Northfield Builders Guild Business card

We are looking for a new business card design with photo included.
Our business is a nonprofit construction contractor membership organization. We offer business education, assist with business setup and licensing, provide safety training, and provide a member directory.
URL: www.builderslinkguild.org
Color code:
CMYK: 0 cyan, 42 magenta, 100 yellow, 0 black for Print.
Hexidecimal: #FF9900
RGB: R 255; G 153; B 0

```html
<!DOCTYPE html>
<html lang="en">
<head>
<meta charset="utf-8">
<title>Northfield Builders Guild — Business Card</title>
<link rel="stylesheet" href="https://fonts.googleapis.com/css2?family=Montserrat:wght@800&family=Arimo:wght@400;700&display=swap">
<style>
  :root {
    --orange: #ff9900;
    --orange-deep: #e8850f;
    --ink: #333333;
    --ink-soft: #555555;
    --paper: #ffffff;
    --rule: #9a9a9a;
    --stage: #2e2e2e;
  }
  * { margin: 0; padding: 0; box-sizing: border-box; }
  html, body { width: 1200px; height: 866px; overflow: hidden; }
  body {
    background: var(--stage);
    font-family: "Arimo", Arial, sans-serif;
    position: relative;
  }
  .card {
    position: absolute;
    top: 278px;
    width: 540px;
    height: 309px;
    overflow: hidden;
    box-shadow: 0 10px 24px rgba(0,0,0,.45);
  }
  .card--front { left: 40px; background: var(--paper); }
  .card--back { left: 620px; }

  .contact { position: absolute; left: 34px; top: 40px; }
  .contact__name {
    font-weight: 700; font-size: 19px; color: var(--orange);
    letter-spacing: .5px; text-transform: uppercase;
  }
  .contact__title {
    font-size: 11px; color: var(--ink-soft); letter-spacing: 1px;
    text-transform: uppercase; margin: 3px 0 14px;
  }
  .contact__list { list-style: none; }
  .contact__item {
    display: flex; align-items: center; gap: 8px;
    font-size: 12.5px; color: var(--ink); height: 19px;
  }
  .contact__icon { width: 14px; height: 14px; flex: none; }

  .divider {
    position: absolute; left: 262px; right: 34px; top: 208px; height: 1px;
    background: var(--rule);
  }

  .brand {
    position: absolute; right: 34px; top: 126px; text-align: right;
    font-family: "Montserrat", Arial, sans-serif; font-weight: 800;
    color: var(--ink); font-size: 30px; line-height: 1.05;
    text-transform: uppercase; letter-spacing: .5px;
  }

  .address {
    position: absolute; right: 34px; bottom: 28px; text-align: right;
    font-size: 13px; color: var(--ink); line-height: 1.35;
  }

  .back__pattern {
    position: absolute; inset: 0;
    background: radial-gradient(circle at 25% 30%, #f59a1c 0%, var(--orange-deep) 55%, #e07f0c 100%);
  }
  .back__brand {
    position: absolute; left: 0; right: 0; top: 50%; transform: translateY(-50%);
    text-align: center;
    font-family: "Montserrat", Arial, sans-serif; font-weight: 800;
    color: var(--paper); font-size: 38px; line-height: 1.08;
    text-transform: uppercase; letter-spacing: .5px;
  }
</style>
</head>
<body>

  <section class="card card--front" aria-label="Business card front">
    <div class="contact">
      <p class="contact__name">Daniel Porter</p>
      <p class="contact__title">Managing Director</p>
      <ul class="contact__list">
        <li class="contact__item">
          <svg class="contact__icon" viewBox="0 0 14 14" aria-hidden="true"><circle cx="7" cy="7" r="7" fill="var(--orange)"/><path d="M4.5 3.5 L6 5 L5.3 6 Q6.3 8 8 8.7 L9 8 L10.5 9.5 L9.5 10.5 Q5.5 10 3.5 4.5 Z" fill="#fff"/></svg>
          (541) 382-7716 (Office)
        </li>
        <li class="contact__item">
          <svg class="contact__icon" viewBox="0 0 14 14" aria-hidden="true"><circle cx="7" cy="7" r="7" fill="var(--orange)"/><rect x="4.8" y="3" width="4.4" height="8" rx=".8" fill="none" stroke="#fff" stroke-width="1.1"/></svg>
          800-555-0192
        </li>
        <li class="contact__item">
          <svg class="contact__icon" viewBox="0 0 14 14" aria-hidden="true"><circle cx="7" cy="7" r="7" fill="var(--orange)"/><rect x="3.5" y="6" width="7" height="4" fill="#fff"/><rect x="5" y="3.5" width="4" height="2.5" fill="none" stroke="#fff" stroke-width="1"/></svg>
          503.555.0147
        </li>
        <li class="contact__item">
          <svg class="contact__icon" viewBox="0 0 14 14" aria-hidden="true"><circle cx="7" cy="7" r="7" fill="var(--orange)"/><rect x="3.5" y="4.5" width="7" height="5" fill="#fff"/><path d="M3.5 4.5 L7 7.5 L10.5 4.5" fill="none" stroke="var(--orange)" stroke-width=".9"/></svg>
          support@nbguild.org
        </li>
        <li class="contact__item">
          <svg class="contact__icon" viewBox="0 0 14 14" aria-hidden="true"><circle cx="7" cy="7" r="7" fill="var(--orange)"/><circle cx="7" cy="7" r="3.6" fill="none" stroke="#fff" stroke-width="1"/><path d="M3.4 7 H10.6 M7 3.4 V10.6" stroke="#fff" stroke-width=".8"/></svg>
          www.builderslinkguild.org
        </li>
      </ul>
    </div>

    <p class="brand">Northfield<br>Builders Guild</p>

    <div class="divider" aria-hidden="true"></div>

    <p class="address">2400 Cedar Mill Rd<br>Suite #210, Salem<br>OR 97301</p>
  </section>

  <section class="card card--back" aria-label="Business card back">
    <div class="back__pattern" role="img" aria-label="Soft orange background with a pattern of large overlapping rings"></div>
    <p class="back__brand">Northfield<br>Builders Guild</p>
  </section>

</body>
</html>
```